KRT Flyer to attract applicants 11x17

Lantern Stagehand Collective provides crew for local concerts, filming, theater, and corporate events.
The flyer will be posted on bulletin boards at colleges with theater programs.
Our primary venues are historic theaters in downtown LA
Need a 11x17 poster to attract potential applicants/crew
I have attached a poster that one of our staff made that has all if the relevant info - but i know the poster can look much better than that. I have also attached many images and our logo. It is not necessary to use all of the images, or any of them. The two images of the theater interiors are the venues we operate so they would be the first to include. I can send additional info or images upon request. Thank you

Industry/Entity Type

Entertainment

Requirements
Must have
• APPLY@KRTCREW.EXAMPLE

```html
<!DOCTYPE html>
<html lang="en">
<head>
<meta charset="utf-8">
<title>KRT — Open Positions</title>
<link rel="stylesheet" href="https://fonts.googleapis.com/css2?family=Fredoka:wght@600;700&family=Titillium+Web:wght@400;700&family=Poppins:wght@300;500;600&display=swap">
<style>
  :root {
    --page-bg: #e2e2e2;
    --paper: #ffffff;
    --paper-shade: #e9e9ec;
    --brand-blue: #2a55a8;
    --box-blue-a: #2c3a9c;
    --box-blue-b: #2356ad;
    --accent-orange: #ee4423;
    --ink-gray: #444447;
    --white: #ffffff;
  }
  * { margin: 0; padding: 0; box-sizing: border-box; }
  html, body { width: 1200px; height: 1200px; overflow: hidden; }
  body { background: var(--page-bg); position: relative; }

  .poster {
    position: absolute;
    left: 253px; top: 58px;
    width: 693px; height: 1071px;
    background: radial-gradient(ellipse at 50% 35%, var(--paper) 45%, var(--paper-shade) 100%);
    box-shadow: 0 6px 14px rgba(0,0,0,0.18);
    overflow: hidden;
  }
  .poster-art { position: absolute; inset: 0; width: 100%; height: 100%; }

  .brand {
    position: absolute; left: 0; right: 0; top: 78px;
    display: flex; align-items: center; justify-content: center; gap: 14px;
  }
  .brand-dot { width: 38px; height: 38px; border-radius: 50%; background: var(--brand-blue); }
  .brand-name {
    font-family: "Titillium Web", sans-serif; font-weight: 700;
    font-size: 28px; line-height: 38px; color: var(--brand-blue);
  }

  .headline {
    position: absolute; left: 0; right: 0; top: 186px;
    text-align: center;
    font-family: "Fredoka", sans-serif; font-weight: 700;
    font-size: 68px; line-height: 1; color: var(--accent-orange);
    letter-spacing: -1.5px; text-transform: uppercase;
  }
  .headline-rule {
    position: absolute; left: 181px; width: 331px; top: 270px;
    height: 3px; background: var(--accent-orange);
  }

  .callout {
    position: absolute; left: 80px; width: 533px; top: 310px; height: 112px;
    border-radius: 11px;
    background: linear-gradient(90deg, var(--box-blue-a), var(--box-blue-b) 60%, var(--box-blue-a));
    color: var(--white); text-align: center;
    font-family: "Titillium Web", sans-serif;
    display: flex; flex-direction: column; justify-content: center;
  }
  .callout-lead { font-weight: 400; font-size: 39px; line-height: 1; }
  .callout-role { font-weight: 700; font-size: 42px; line-height: 1.05; }

  .subline {
    position: absolute; left: 0; right: 0; top: 438px;
    text-align: center;
    font-family: "Poppins", sans-serif; font-weight: 300;
    font-size: 30px; line-height: 35px; color: var(--ink-gray);
  }

  .apply-label {
    position: absolute; left: 0; right: 0; top: 890px;
    text-align: center; color: var(--white);
    font-family: "Poppins", sans-serif; font-weight: 500; font-size: 22px; line-height: 28px;
  }
  .apply-email {
    position: absolute; left: 50%; top: 922px; transform: translateX(-50%);
    height: 46px; padding: 0 20px;
    display: flex; align-items: center; white-space: nowrap;
    background: var(--accent-orange); border-radius: 11px;
    border: 1px solid rgba(255,255,255,0.6);
    color: var(--white);
    font-family: "Poppins", sans-serif; font-weight: 600; font-size: 24px;
  }

  .site {
    position: absolute; left: 0; right: 0; top: 1012px; height: 22px;
    display: flex; align-items: center; gap: 16px;
    color: var(--white);
  }
  .site-rule { flex: 1; height: 2px; background: rgba(255,255,255,0.85); }
  .site-url {
    font-family: "Poppins", sans-serif; font-weight: 600; font-size: 14px;
    letter-spacing: 6px; margin-right: -6px; white-space: nowrap;
  }
</style>
</head>
<body>
  <main class="poster">
    <svg class="poster-art" viewBox="0 0 1116 1724" preserveAspectRatio="none">
      <defs>
        <linearGradient id="bandGradient" x1="0" y1="0" x2="1" y2="1">
          <stop offset="0" stop-color="#c6233a"/>
          <stop offset="0.45" stop-color="#6b2d86"/>
          <stop offset="1" stop-color="#323799"/>
        </linearGradient>
        <linearGradient id="venueDome" x1="0" y1="0" x2="1" y2="1">
          <stop offset="0" stop-color="#4a1f5e"/>
          <stop offset="0.5" stop-color="#a0523c"/>
          <stop offset="1" stop-color="#3b1f5c"/>
        </linearGradient>
        <linearGradient id="venueHall" x1="0" y1="0" x2="1" y2="1">
          <stop offset="0" stop-color="#8a4a1c"/>
          <stop offset="0.5" stop-color="#d7943e"/>
          <stop offset="1" stop-color="#5a2a12"/>
        </linearGradient>
      </defs>
      <rect class="band" x="0" y="1240" width="1116" height="484" fill="url(#bandGradient)" role="img" aria-label="Blurred night skyline of downtown Los Angeles"/>
      <path class="band-edge" fill="#ffffff"
            d="M0,1240 L0,1247 C180,1340 400,1385 642,1262 C820,1370 960,1440 1116,1452 L1116,1240 Z"/>
      <path class="venue-photo venue-photo--dome" fill="url(#venueDome)" role="img"
            aria-label="Photo of an ornate historic theater auditorium with a lit dome and stage"
            d="M0,865 C250,855 440,920 525,1035 C570,1110 610,1190 642,1262 C440,1350 200,1340 0,1200 Z"/>
      <path class="venue-photo venue-photo--hall" fill="url(#venueHall)" role="img"
            aria-label="Photo of a gilded historic theater interior with balconies and boxes"
            d="M520,1045 C700,900 900,880 1116,735 L1116,1407 C950,1395 820,1350 720,1290 C640,1230 575,1150 520,1045 Z"/>
    </svg>

    <header class="brand">
      <span class="brand-dot"></span>
      <span class="brand-name">Lantern Stagehand Collective</span>
    </header>

    <h1 class="headline">Open Positions</h1>
    <div class="headline-rule"></div>

    <section class="callout">
      <p class="callout-lead">WE ARE LOOKING FOR</p>
      <p class="callout-role">TALENTED TECHNICIANS</p>
    </section>

    <p class="subline">TO ADD TO OUR ROSTER OF<br>SKILLED PROFESSIONALS</p>

    <p class="apply-label">Send Resume to:</p>
    <p class="apply-email">APPLY@KRTCREW.EXAMPLE</p>

    <footer class="site">
      <span class="site-rule"></span>
      <span class="site-url">WWW.KRTCREW.EXAMPLE</span>
      <span class="site-rule"></span>
    </footer>
  </main>
</body>
</html>
```